Moxy Fen needs some awesome stationary

Do you have what it takes to get my brand? You either do or you don't, have a crack at a design and you my just win my business.

I don't want to waste your or my time, so put your creative genius on either a business card or envelope.

I however need a package of stationary that follows the same brand. I will message you to complete the remaining should I like your first submission.

Here is what I need, have a go!

Basically I need the following for my small business based in melbourne.
- Letterhead (printer ready and MS Word)
- Business Card
- Compliments Slip
- Envelope
- Proposal Cover Page (MS Word only)
- Presentation Folder
- Marbled Fox Cards
- Student Name Tent
- Index Cards
- Vell-Ka

I am establishing the brand and it must be modern, professional but also relaxed; that is not formal and not corporate. It represents a company are leaders, but small enough to care and operate like a bunch of friends. We are bringing people and conversations back to business, and turfing out all the bureaucracy and crazy and wasteful procedures. Its about "lets talk and figure it out together and find even better ways".

Target Market(s)

Mainly companies that build software products, but Agile practices are used in many other industries (even graphic design projects)

Industry/Entity Type

Information Technology

Font styles to use
Sans Serif

Colors
3176b5
aaaaaa

Requirements
Must have
• I like curves and circles and not boxes or rectangles.
• I want a colour rich design with my brand colours, but it must be balanced.
• I want more modern than traditional, but simple modern
Should not have
• Not corporate
• Please don't waste my time if your not going to think about it.
• Don't mess with my primary logo
• Don't change my colours
• Don't overlay logo on image

```html
<!DOCTYPE html>
<html lang="en">
<head>
<meta charset="utf-8">
<title>Moxy Fen — Business Card</title>
<link rel="stylesheet" href="https://fonts.googleapis.com/css2?family=Open+Sans:wght@400;600;700&display=swap">
<style>
  :root {
    --brand-blue: #2b5aa1;
    --brand-grey: #96a0ad;
    --ink: #3d3d3d;
    --paper: #ffffff;
    --backdrop: #ebebeb;
    --rule: #d9d9d9;
    --edge-line: #9aa6b6;
  }
  * { box-sizing: border-box; margin: 0; padding: 0; }
  html, body {
    width: 1200px; height: 987px; overflow: hidden;
    background: var(--backdrop);
    font-family: "Open Sans", Arial, sans-serif;
  }
  .stage { position: relative; width: 1200px; height: 987px; }
  .card {
    position: absolute; left: 293px; width: 615px; height: 350px;
    border-radius: 20px; overflow: hidden;
    box-shadow: 0 3px 10px rgba(0,0,0,0.18);
  }
  .card--front { top: 131px; background: var(--paper); }
  .card--back { top: 506px; background: var(--brand-blue); }

  .brand { position: absolute; display: flex; align-items: center; gap: 10px; font-weight: 700; white-space: nowrap; }
  .brand__dot { border-radius: 50%; flex: none; }
  .card--front .brand { left: 66px; top: 154px; color: var(--brand-blue); font-size: 32px; }
  .card--front .brand__dot { width: 28px; height: 28px; background: var(--brand-grey); }

  .divider { position: absolute; left: 290px; top: 56px; width: 1px; height: 241px; background: var(--rule); }

  .details { position: absolute; left: 315px; top: 56px; color: var(--ink); }
  .details__name { font-size: 22px; font-weight: 600; color: var(--brand-blue); line-height: 28px; }
  .details__title { font-size: 16.5px; color: var(--brand-grey); line-height: 22px; margin-bottom: 12px; white-space: nowrap; }
  .details__address { font-size: 16px; line-height: 22px; font-style: normal; margin-bottom: 8px; }
  .contact { list-style: none; font-size: 16px; line-height: 23.5px; }
  .contact li { display: flex; align-items: center; gap: 8px; }
  .contact svg { width: 14px; height: 14px; fill: var(--brand-blue); flex: none; }

  .edge-rule { position: absolute; left: 0; right: 0; top: 321px; height: 2px; background: var(--edge-line); }
  .edge-band { position: absolute; left: 0; right: 0; top: 327px; bottom: 0; background: var(--brand-blue); }

  .card--back .brand { left: 380px; top: 240px; color: var(--paper); font-size: 28px; }
  .card--back .brand__dot { width: 26px; height: 26px; background: var(--paper); }
  .back__web { position: absolute; left: 393px; top: 299px; color: var(--paper); font-size: 15.5px; }
</style>
</head>
<body>
<main class="stage">
  <section class="card card--front" aria-label="Business card front">
    <div class="brand"><span class="brand__dot"></span><span>Moxy Fen</span></div>
    <div class="divider"></div>
    <div class="details">
      <p class="details__name">Dana Whitcombe</p>
      <p class="details__title">CEO, Lead Agile Coach &amp; Mentor</p>
      <address class="details__address">PO Box 4417<br>Ferncliff East<br>VIC 3190, Australia</address>
      <ul class="contact">
        <li><svg viewBox="0 0 16 16"><path d="M3.5 1l2.5 3-1.5 1.6c.8 2 2.4 3.6 4.4 4.4L10.5 8.5l3 2.5-1.5 3C6.5 13.5 2.5 9.5 2 4z"/></svg>1300MOXYF</li>
        <li><svg viewBox="0 0 16 16"><path d="M4 1h8v14H4zM5.5 2.5v9h5v-9zM7.2 12.5h1.6v1.3H7.2z" fill-rule="evenodd"/></svg>+61 412 507 318</li>
        <li><svg viewBox="0 0 16 16"><path d="M1 3.5h14v9H1z"/><path d="M1.5 4l6.5 5 6.5-5" fill="none" stroke="#fff" stroke-width="1"/></svg>dana@moxy-fen.com.au</li>
        <li><svg viewBox="0 0 16 16"><circle cx="8" cy="8" r="7"/><path d="M5 4c2 1 1 3 3 3s1 3-1 4M10 3c1 2 3 2 3 4" fill="none" stroke="#fff" stroke-width="1.2"/></svg>www.moxy-fen.com.au</li>
      </ul>
    </div>
    <div class="edge-rule"></div>
    <div class="edge-band"></div>
  </section>

  <section class="card card--back" aria-label="Business card back">
    <div class="brand"><span class="brand__dot"></span><span>Moxy Fen</span></div>
    <p class="back__web">www.moxy-fen.com.au</p>
  </section>
</main>
</body>
</html>
```